Nutritional & Gastrointestinal Health Consulting Service-Website design

We need a website design for a new health consulting service called "Bright Vale" based in Perth, Australia.

We will be providing consulting services in the areas of:
1) Nutrition and Diet
2) Gastrointestinal Health (which means stomach & digestive system related health)

These consulting services will be provided by an Accredited Dietitian and a Paediatric Gastroenterologist.

We are open to creative ideas in terms of design, layout, fonts and colours. We also would love to see images of nature in the backdrop with families (adults with kids) having a good time, fresh fruits and vegetables displayed in a farmer's market or supermarket. 2 or 3 images should be sufficient. We would also definitely want our logo somewhere in the main page of website. The logo file is also attached. Please have a look at a website's design that we really liked. We would love to see designs inspired by that style. The website details are in the in the "nice to have priorities" section of this project brief.

We also would be looking at website designers with software coding skills so that if we like the design we can go ahead with the next step of coding.

The website design should communicate the purpose of the website and at the same time be simple, elegant and unique/eye-catching.

We look forward to receiving creative ideas for our website from you all. Good luck!

More details have been added to our project- for example: Logo, fonts style, must haves etc etc. Please view the updated project brief. Looking forward to receiving your fantastic ideas for our website. Thanking you

Hi, I have updated the colour preference. Will add the content preferences tomorrow. thanks

Hello all, I have now added a LOT more content to what we want in our website. It is very much in detail, so please carefully have a read through the entire project brief. If you have any questions write back to me and I will try to respond as quickly as I can. Last few days were busy so couldn't respond quickly to all of you who had send me designs/queries/questions. Thank you for your patience. I look forward to receiving fantastic designs from you all. Good Luck :-)

Target Market(s)

Adults based in western speaking countries aged 18 to 60 years

Industry/Entity Type

Software

Font styles to use
Sans Serif
Script

Colors
faa54b
acd036

Requirements
Must have
• The website must have the MAIN logo file attached. I have attached 3 files: 1) MAIN logo; 2) supplementary logo A ; 3) supplementary logo B

I have selected 2 colours from the colour scheme (see below)-(as the colour of our logo is that).
However we would also like to see LIGHT CHOCOLATE BROWN or CHOCOLATE BROWN colour used as the background colour of the website
Preferred WEBSITE CONTENT:
1) HOME PAGE:
Content required=
--Company Logo
--Dr Dorian Pelham
Paediatric Gastroenterologist & Hepatologist
-Marla Pelham.
Dietitian & Nutritionist
--Website Menu (either listed horizontally or vertically):
Once clicked on each name:

Under each of the Website Menu items we want the following Headings to be added

2) ABOUT US page:
Sub-heading under this: Qualification, Skills, Special Interest

3) SERVICES
DORIAN'S PAGE: Individual Consultation, Endoscopy procedures
Individual Consultation, Group Based Services, Food Diary, Food & Symptom Diary

4) FEES & REBATE: Content as below:
Please Note: Payment of full fees is required at the time of consultation and procedures. 48 hours notice is required for cancellation of appointments/non-attendance. Failure to provide this may result in a fee being incurred. Please call reception to find out the amount of fee charged for cancellation of appointments/non-attendance.
headings are:
Paediatric Gastroenterology:
Dorian's pge
Individual Consultation - Initial (upto 30 mins):
Review Consultation (upto 15 mins):
Endoscopy procedures - No Gap fees charged. Fees will be billed directly to Vitacover. If any queries, please contact reception.

marla's pge
sub heading:
Individual Consultation - Initial (upto 45 mins):
Individual Consultation - Review (upto 30 mins):

Concession-Individual Consultation -Initial (upto 45 mins):
Concession-Individual Consultation - Review (upto 30 mins):
Please Note: Concession applies for health care card holders & pensioners

Group Based Services: Pricing subject to the type of service provided. Please contact us for an obligation free quote.
Education Topics Include:
- Paediatric Nutrition (Introducing Solids, Fussy Eating, Healthy Eating)
- Pregnancy Nutrition, Gestational Diabetes, Breastfeeding/Lactation Nutrition
- Healthy Eating, Supermarket Shopping Tips, Nutrition Label Reading Tips, Healthier
sub heading under nutrition & diet:
-Vitacover:
--A rebate of $52.95 is available from Vitacover if an EPC ( Enhanced Primary Care)/Chronic Disease Management (CDM) plan is issued by your GP.
--All mandatory paperwork needs to be available at the time of making your appointment for your eligibility.
-Private Health Fund:
--Most private health funds provide rebate on dietetic appointments. However the rebate amount depends on your level of cover. Thus, please contact your health fund to determine your entitled rebate.
-RSB: Approved provider for RSB services

6) FOR DOCTORS: Bright Vale Paediatric Gastroenterologist Referral Form
Bright Vale Dietitian Referral form
7) LOCATIONS & CONTACT

Paediatric Gastroenterology & Hepatology Service
Suite 46
Holy Lantern Bramcote Medical Centre
17 Colin Ferris Pde,
MURDOCH, WA 6150
P: (08) 9422 5061
F: (08) 9422 3094

Nutrition & Diet Service
Suite 46
17 Colin Ferris Pde,
MURDOCH, WA 6150
P: (08) 9422 5061
F: (08) 9422 3094

Tolland Medical Centre
58-60 Karrigan Parkway,
MANDURAH, WA 6210
P: (08) 9647 2283
F: (08) 96724419
www.tmcexample.com.au

This page should have a webform that has following titles:
-Your Name
-Your Email
-Your Phone
-Message

8) NEWS & BLOG
Nice to have
• We liked the design style of the websites below:
https://www.vendoraplex.example/

http://qoravelt.example/

But feel free to use your creativity too
Should not have
• Please do not use any body building or muscle building images

```html
<!DOCTYPE html>
<html lang="en">
<head>
<meta charset="utf-8">
<title>Bright Vale – About Us</title>
<link href="https://fonts.googleapis.com/css2?family=Arimo:wght@400;700&family=Open+Sans:wght@600;700&display=swap" rel="stylesheet">
<style>
:root{
  --page-bg:#5c3b1f;
  --frame-bg:#c6b7aa;
  --content-bg:#d7cdc6;
  --panel-bg:#8a6b55;
  --photo-bg:#76553a;
  --edge:#f4f1ee;
  --ink:#111;
  --heading:#5a3a1e;
  --menu-link:#f0ee5a;
  --menu-active:#faa54b;
  --green:#acd036;
  --orange:#faa54b;
  --top-link:#6e5030;
}
*{box-sizing:border-box;margin:0;padding:0}
html,body{width:1021px;height:1200px;overflow:hidden}
body{background:var(--page-bg);font-family:"Open Sans",sans-serif;color:var(--ink);position:relative}
.page-bg{position:absolute;inset:0;background:linear-gradient(135deg,#6a4526,#553619)}
.frame{position:absolute;left:30px;top:31px;width:960px;height:1135px;background:var(--frame-bg);border:3px solid var(--edge);border-radius:12px}
.account-links{position:absolute;left:870px;top:38px;font-family:Arimo,sans-serif;font-size:11px;color:var(--top-link)}
.account-links a{color:var(--top-link)}
.account-links .sep{margin:0 6px;color:#fff}
.masthead{position:absolute;left:212px;top:53px;width:594px;height:149px;background:var(--panel-bg);border:3px solid var(--edge);border-radius:12px;display:flex;flex-direction:column;align-items:center;justify-content:center;gap:8px}
.brand-mark{width:40px;height:40px;border-radius:50%;background:var(--orange)}
.brand-name{font-family:Arimo,sans-serif;font-weight:700;font-size:28px;color:var(--green);letter-spacing:1px}
.panel{position:absolute;background:var(--panel-bg);border:3px solid var(--edge);border-radius:6px}
.panel-title{height:24px;border-bottom:2px solid var(--edge);text-align:center;font-family:Arimo,sans-serif;font-weight:700;font-size:12.5px;color:#fff;line-height:22px}
.main-menu{left:53px;top:219px;width:189px;height:206px}
.main-menu ul{margin:20px 0 0 50px;list-style:circle;color:var(--menu-link);font-size:10.5px;line-height:15px}
.main-menu li{padding-left:0}
.main-menu a{color:var(--menu-link);font-weight:700}
.main-menu a.current{color:var(--menu-active)}
.user-login{left:778px;top:219px;width:189px;height:181px}
.login-form{padding:14px 0 0 12px;font-family:Arimo,sans-serif;font-size:10.5px;color:#fff;font-weight:700}
.login-form .req{color:#e33}
.login-form .field{width:92px;height:17px;background:#fff;border:1px solid #999;color:#000;font-weight:400;font-size:11px;padding:1px 2px;margin:2px 0 6px}
.login-form .reset{margin:6px 0 0 8px;font-weight:400;list-style:disc;padding-left:10px}
.login-form .reset a{color:var(--menu-link)}
.login-form .btn{margin-top:10px;display:inline-block;background:#eee;border:1px solid #888;border-radius:2px;color:#000;font-weight:400;padding:1px 7px;font-size:10px}
.content{position:absolute;left:252px;top:219px;width:516px;height:894px;background:var(--content-bg);border:3px solid var(--edge);border-radius:6px}
.breadcrumb{position:absolute;left:16px;top:4px;width:490px;border-bottom:2px solid #fff;padding-bottom:2px;font-family:Arimo,sans-serif;font-weight:700;font-size:10.5px}
.breadcrumb a{color:var(--ink)}
.page-title{position:absolute;left:9px;top:30px;font-family:Arimo,sans-serif;font-weight:700;font-size:17px;color:var(--heading)}
.profile{position:absolute;width:290px;font-size:10.2px;line-height:12.8px}
.profile h2{font-family:Arimo,sans-serif;font-size:18px;text-decoration:underline;margin-bottom:14px}
.profile .role{font-family:Arimo,sans-serif;font-weight:700;font-size:13.5px;line-height:14px;margin-bottom:10px}
.profile h3{font-family:Arimo,sans-serif;font-size:12px;text-decoration:underline;margin:10px 0 12px}
.profile p{margin-bottom:6px}
.doctor{left:23px;top:74px}
.dietitian{left:211px;top:500px}
.photo{position:absolute;width:174px;height:227px;background:var(--photo-bg);border:3px solid var(--edge);border-radius:18px;display:flex;align-items:center;justify-content:center;text-align:center;font-family:Arimo,sans-serif;font-style:italic;font-size:22px;line-height:27px;color:#111}
.photo-doctor{left:319px;top:77px}
.photo-dietitian{left:23px;top:502px}
.rule{position:absolute;left:21px;width:474px;border-top:2px solid #f2eeea}
.footer{position:absolute;left:0;width:1021px;top:1133px;text-align:center;font-weight:700;font-size:10.5px}
.footer a{color:var(--ink)}
</style>
</head>
<body>
<div class="page-bg" role="img" aria-label="Chocolate brown background with a faint food doodle pattern"></div>
<div class="frame" role="img" aria-label="Light brown page area with a faint food doodle pattern"></div>

<div class="account-links"><a href="#">Login</a><span class="sep">|</span><a href="#">Register</a></div>

<header class="masthead">
  <span class="brand-mark"></span>
  <span class="brand-name">Bright Vale</span>
</header>

<nav class="panel main-menu">
  <div class="panel-title">Main menu</div>
  <ul>
    <li><a class="current" href="#">Home</a></li>
    <li><a class="current" href="#">About Us</a></li>
    <li><a href="#">Nutrition &amp; Diet</a></li>
    <li><a href="#">Paediatric Gastroenterology</a></li>
    <li><a href="#">Fees &amp; Rebate</a></li>
    <li><a href="#">For Doctors</a></li>
    <li><a href="#">Location</a></li>
    <li><a href="#">Contact</a></li>
    <li><a href="#">News &amp; Blog</a></li>
  </ul>
</nav>

<aside class="panel user-login">
  <div class="panel-title">User login</div>
  <div class="login-form">
    <div>Username <span class="req">*</span></div>
    <div class="field">guest</div>
    <div>Password <span class="req">*</span></div>
    <div class="field">●●●●●●●●●●●</div>
    <ul class="reset"><li><a href="#">Request new password</a></li></ul>
    <span class="btn">Log in</span>
  </div>
</aside>

<main class="content">
  <div class="breadcrumb"><a href="#">Home</a></div>
  <h1 class="page-title">About Us</h1>

  <section class="profile doctor">
    <h2>Dr. Dorian Pelham</h2>
    <div class="role">Paediatric Gastroenterologist<br>&amp; Hepatologist</div>
    <h3>Qualifications</h3>
    <p>Donec non posuere arcu. Nulla non lobortis sapien, eget mattis orci. Suspendisse in malesuada justo. Nunc varius dolor vel est porttitor porttitor. Nunc vestibulum urna quis sollicitudin fringilla.</p>
    <h3>Skills</h3>
    <p>Mauris non elit et tellus aliquam porttitor. Pellentesque ac nunc gravida arcu suscipit fermentum. Etiam luctus vulputate dapibus. Pellentesque facilisis sapien vel nulla lacinia scelerisque.</p>
    <h3>Special Interest</h3>
    <p>Sed congue maximus nulla eget venenatis. Curabitur sapien lacus, maximus vitae vehicula dapibus, molestie at nibh. Nulla dolor nisl, viverra ut faucibus in, fringilla nec tellus. Donec consequat, arcu vitae facilisis lacinia, lacus velit sagittis leo, in maximus nunc mi eget dolor.</p>
  </section>
  <div class="photo photo-doctor" role="img" aria-label="Portrait of the doctor">Photo of<br>Doctor</div>

  <div class="rule" style="top:472px"></div>

  <div class="photo photo-dietitian" role="img" aria-label="Portrait of the dietitian">Photo of<br>Dietitian</div>
  <section class="profile dietitian">
    <h2>Marla Pelham</h2>
    <div class="role">Accredited Practising Dietitian</div>
    <h3>Qualifications</h3>
    <p>Etiam eget est a libero molestie hendrerit. Aliquam nunc velit, dictum vel sem a, placerat venenatis quam. Proin ut nulla lorem. Duis eu pulvinar dui. Nunc eget massa diam.</p>
    <h3>Skills</h3>
    <p>Vestibulum mattis viverra lorem ut suscipit. Nam in luctus dolor. Vestibulum at vehicula est. Quisque sed bibendum massa. In ut viverra orci, ac scelerisque augue. Cras ultricies mollis diam ac viverra.</p>
    <h3>Special Interest</h3>
    <p>Praesent tempor eros lacinia nisi posuere fringilla. Donec eget ex lobortis, sodales dui ultrices, tincidunt ante. Nullam dictum mauris sit amet nibh malesuada iaculis. Aenean eu metus venenatis, feugiat magna eu, porttitor tellus. Nunc egestas lorem et ipsum facilisis efficitur.</p>
  </section>

  <div class="rule" style="top:872px"></div>
</main>

<footer class="footer"><a href="#">Bright Vale</a> © Copyright 2014</footer>
</body>
</html>
```